Business Card Design - Property Management & Real Estate Services

I need a business card design for my company that I can print ZEPLA Cards. The company is called Brindle Management Company. It is a property management and real estate company. The design has to be clean and modern. I need two versions. One for my employee and one for me. However, the design will be the same, just different text. You can get a feel for the company by looking at our website at www.brindlemanagement.example.

Industry/Entity Type

Property Management

Contact Information for Business Card

I will be using ZEPLA.com to print my cards. I will most likely use the rounded edges card. I need two versions, however, they will be the same design. I need one for me and my employee.

Colors
3276b5
33a6d7

Requirements
Must have
• Company Logo
• Name of person
• Property Management & Real Estate Service
• Phone
• Email
• Website
• Address
• A space to place a QR code

```html
<!DOCTYPE html>
<html lang="en">
<head>
<meta charset="utf-8">
<title>Brindle Management – Business Card</title>
<link href="https://fonts.googleapis.com/css2?family=Roboto:wght@400;500&family=Roboto+Condensed:wght@700&display=swap" rel="stylesheet">
<style>
  :root {
    --backdrop: #c9c9c9;
    --card-white: #f7f7f7;
    --card-blue: #6699cc;
    --brand-deep: #1f55a4;
    --brand-mid: #3276b5;
    --brand-light: #33a6d7;
    --ink: #3a3a3a;
  }
  * { box-sizing: border-box; margin: 0; padding: 0; }
  html, body {
    width: 1200px; height: 852px; overflow: hidden;
    background: var(--backdrop);
    font-family: "Roboto", Arial, sans-serif;
  }
  .stage {
    position: relative; width: 1200px; height: 852px;
    display: flex; align-items: center; justify-content: center; gap: 50px;
  }
  .card {
    position: relative; width: 490px; height: 280px;
    border-radius: 16px; overflow: hidden;
    box-shadow: 0 3px 8px rgba(0,0,0,.18);
  }
  /* back side */
  .card--back {
    background: var(--card-blue);
    display: flex; align-items: center; justify-content: center;
  }
  .wordmark {
    display: flex; align-items: center; gap: 12px;
    color: var(--brand-deep); font-weight: 500;
  }
  .wordmark__square { width: 22px; height: 22px; background: currentColor; flex: none; }
  .wordmark__name { font-size: 36px; letter-spacing: 1px; line-height: 1.1; }
  /* front side */
  .card--front { background: var(--card-white); }
  .front__logo {
    position: absolute; left: 30px; top: 110px; width: 180px;
  }
  .front__logo .wordmark { color: var(--brand-mid); gap: 10px; }
  .front__logo .wordmark__name { font-size: 24px; letter-spacing: .5px; }
  .front__logo .wordmark__square { width: 16px; height: 16px; }
  .front__details { position: absolute; left: 228px; top: 44px; width: 250px; }
  .person__name {
    font-family: "Roboto Condensed", "Arial Narrow", sans-serif;
    font-weight: 700; font-size: 19px; color: var(--brand-deep);
  }
  .person__title { font-size: 12px; color: var(--ink); margin-top: 4px; }
  .contact { list-style: none; margin-top: 16px; }
  .contact__item {
    display: flex; align-items: center; gap: 8px;
    font-size: 12px; color: var(--ink); line-height: 19px;
    white-space: nowrap;
  }
  .contact__icon { width: 11px; height: 11px; fill: var(--brand-deep); flex: none; }
  .front__rule {
    position: absolute; left: 0; right: 0; bottom: 48px;
    height: 2px; background: var(--brand-mid);
  }
  .front__band {
    position: absolute; left: 0; right: 0; bottom: 0; height: 42px;
    background: var(--brand-deep); color: #fff;
    display: flex; align-items: center; justify-content: center;
    font-size: 14px; letter-spacing: .2px;
  }
</style>
</head>
<body>
<main class="stage">
  <section class="card card--back" aria-label="Card back">
    <div class="wordmark">
      <span class="wordmark__square"></span>
      <span class="wordmark__name">Brindle Management</span>
    </div>
  </section>

  <section class="card card--front" aria-label="Card front">
    <div class="front__logo">
      <div class="wordmark">
        <span class="wordmark__square"></span>
        <span class="wordmark__name">Brindle<br>Management</span>
      </div>
    </div>

    <div class="front__details">
      <h1 class="person__name">Marisol T. Ortega</h1>
      <p class="person__title">Founder</p>
      <ul class="contact">
        <li class="contact__item">
          <svg class="contact__icon" viewBox="0 0 24 24"><path d="M6.6 10.8a15.1 15.1 0 0 0 6.6 6.6l2.2-2.2a1 1 0 0 1 1-.25 11.4 11.4 0 0 0 3.6.57 1 1 0 0 1 1 1V20a1 1 0 0 1-1 1A17 17 0 0 1 3 4a1 1 0 0 1 1-1h3.5a1 1 0 0 1 1 1c0 1.25.2 2.45.57 3.57a1 1 0 0 1-.25 1z"/></svg>
          (305) 555-0142
        </li>
        <li class="contact__item">
          <svg class="contact__icon" viewBox="0 0 24 24"><path d="M2 5h20v14H2z M3.5 6.5 12 13l8.5-6.5" fill="none" stroke="var(--brand-deep)" stroke-width="2.4"/></svg>
          marisol@brindlemanagement.example
        </li>
        <li class="contact__item">
          <svg class="contact__icon" viewBox="0 0 24 24"><circle cx="12" cy="12" r="10"/><path d="M2 12h20M12 2c3 3 3 17 0 20M12 2c-3 3-3 17 0 20" stroke="#fff" stroke-width="1.6" fill="none"/></svg>
          www.brindlemanagement.example
        </li>
      </ul>
    </div>

    <div class="front__rule"></div>
    <footer class="front__band">480 Harbor View Ave #300 Miami, FL 33131</footer>
  </section>
</main>
</body>
</html>
```